Coastline Premier Retreats Business Card Design

Design a business card for Coastline Premier Retreats. Look at the website for colors and reference. Card should have logo, name, title, office number, mobile number, email, URL and a tagline like, "Luxury Hotel & Resort Email Marketing" (This might change).

https://www.coastlinepremierretreats.example

The rest I will leave up to your imagination.

Contact Information for Business Card

Logo, name, title, office number, mobile number, email, URL and a tagline like, "Luxury Hotel & Resort Email Marketing" (This might change).

```html
<!DOCTYPE html>
<html lang="en">
<head>
<meta charset="utf-8">
<title>Coastline Premier Retreats – Business Card</title>
<link rel="stylesheet" href="https://fonts.googleapis.com/css2?family=Arimo:wght@400;700&display=swap">
<style>
  :root {
    --backdrop: #b9b8b9;
    --card-white: #ffffff;
    --ink-black: #1c1c1c;
    --deep-black: #050505;
    --accent-orange: #f47a1f;
    --accent-navy: #0b0c3d;
    --text-gray: #6f6f6f;
    --text-white: #ffffff;
  }
  * { box-sizing: border-box; margin: 0; padding: 0; }
  html, body { width: 1200px; height: 876px; overflow: hidden; }
  body {
    background: var(--backdrop);
    font-family: "Arimo", Arial, sans-serif;
    position: relative;
  }
  .card {
    position: absolute;
    width: 500px;
    height: 286px;
    top: 295px;
    overflow: hidden;
    box-shadow: 0 6px 18px rgba(0,0,0,0.25);
  }
  .card--front { left: 70px; background: var(--card-white); }
  .card--back {
    left: 630px;
    background: radial-gradient(ellipse at 35% 45%, #333 0%, #141414 45%, var(--deep-black) 100%);
  }

  /* front */
  .name-band {
    position: absolute;
    left: 0; top: 30px;
    width: 236px; height: 38px;
    background: var(--ink-black);
    padding: 6px 0 0 22px;
  }
  .name-band .person-name {
    color: var(--accent-orange);
    font-weight: 700;
    font-size: 14px;
    letter-spacing: 0.2px;
    white-space: nowrap;
  }
  .name-band .person-title {
    color: var(--text-white);
    font-size: 9px;
    margin-top: 2px;
  }
  .navy-tab {
    position: absolute;
    right: 0; top: 82px;
    width: 34px; height: 42px;
    background: var(--accent-navy);
  }
  .brand {
    position: absolute;
    display: flex;
    align-items: center;
    gap: 8px;
  }
  .brand__mark {
    width: 12px; height: 12px;
    background: var(--accent-orange);
    flex: none;
  }
  .brand__name {
    font-weight: 700;
    line-height: 1.1;
    text-transform: uppercase;
    letter-spacing: 1px;
    white-space: nowrap;
  }
  .card--front .brand { left: 250px; top: 36px; }
  .card--front .brand__name { color: var(--ink-black); font-size: 16px; }
  .card--back .brand { left: 50%; top: 50%; transform: translate(-50%, -50%); }
  .card--back .brand__name { color: var(--text-white); font-size: 24px; }

  .contact-list {
    position: absolute;
    left: 30px; top: 112px;
    list-style: none;
  }
  .contact-list li {
    display: flex;
    align-items: center;
    gap: 7px;
    color: var(--text-gray);
    font-size: 11px;
    line-height: 17px;
    white-space: nowrap;
  }
  .contact-list svg { width: 10px; height: 10px; flex: none; }
  .address {
    position: absolute;
    right: 40px; bottom: 26px;
    text-align: right;
    color: var(--text-gray);
    font-size: 13px;
    line-height: 18px;
    font-style: normal;
  }
</style>
</head>
<body>
  <section class="card card--front" aria-label="Business card front">
    <div class="name-band">
      <p class="person-name">DANIEL HARTLEY</p>
      <p class="person-title">Manager</p>
    </div>
    <div class="brand">
      <span class="brand__mark"></span>
      <p class="brand__name">Coastline<br>Premier Retreats</p>
    </div>
    <div class="navy-tab"></div>
    <ul class="contact-list">
      <li>
        <svg viewBox="0 0 10 10" aria-hidden="true"><path d="M2 1l2 2-1 1.2c.6 1.2 1.6 2.2 2.8 2.8L7 6l2 2-1.3 1.3C4.5 9 1 5.5.7 2.3z" fill="var(--accent-orange)"/></svg>
        123-456-2100
      </li>
      <li>
        <svg viewBox="0 0 10 10" aria-hidden="true"><rect x="2.5" y="0.5" width="5" height="9" rx="1" fill="none" stroke="var(--accent-orange)"/><circle cx="5" cy="8" r=".6" fill="var(--accent-orange)"/></svg>
        123-456-2100
      </li>
      <li>
        <svg viewBox="0 0 10 10" aria-hidden="true"><rect x=".5" y="2" width="9" height="6.5" fill="none" stroke="var(--accent-orange)"/><path d="M.5 2L5 5.6 9.5 2" fill="none" stroke="var(--accent-orange)"/></svg>
        hello@coastlinepremierretreats.example
      </li>
      <li>
        <svg viewBox="0 0 10 10" aria-hidden="true"><circle cx="5" cy="5" r="4.5" fill="var(--accent-orange)"/><path d="M.5 5h9M5 .5c-2 2.5-2 6.5 0 9M5 .5c2 2.5 2 6.5 0 9" fill="none" stroke="#fff" stroke-width=".6"/></svg>
        www.coastlinepremierretreats.example
      </li>
    </ul>
    <address class="address">Your Address, City<br>State, Zip 0000</address>
  </section>

  <section class="card card--back" aria-label="Business card back">
    <div class="brand">
      <span class="brand__mark"></span>
      <p class="brand__name">Coastline<br>Premier Retreats</p>
    </div>
  </section>
</body>
</html>
```